Business Card Design

New business card design

Target Market(s)

Residential & Commercial Property Managers

Industry/Entity Type

Plumbing Services

Contact Information for Business Card

Name - Rowan Keddle, title - Director, Phone Number - 0431 286 517, email - rowan@tbk-plumbing.com.au, Company ABN - 73 215 904 386,

Font styles to use
Sans Serif

Colors
0054AA
0677BA
7BADD7
CADEEF
E8F1F8

```html
<!DOCTYPE html>
<html lang="en">
<head>
<meta charset="utf-8">
<title>TBK Plumbing Services – Business Card</title>
<link rel="stylesheet" href="https://fonts.googleapis.com/css2?family=Poppins:wght@300;400;500;600&display=swap">
<style>
  :root {
    --stage: #222222;
    --paper: #ffffff;
    --water: #27a7e0;
    --earth: #6b6157;
    --ink: #1c2633;
    --muted: #7a7067;
    --logo-light: #ececec;
  }
  * { box-sizing: border-box; margin: 0; padding: 0; }
  html, body {
    width: 1200px; height: 780px; overflow: hidden;
    background: var(--stage);
    font-family: "Poppins", sans-serif;
  }
  .stage {
    position: relative; width: 1200px; height: 780px;
    display: flex; align-items: center; justify-content: center; gap: 44px;
  }
  .card {
    position: relative; width: 520px; height: 297px;
    border-radius: 22px; overflow: hidden;
  }
  .card--front { background: var(--paper); }
  .card--back { background: var(--earth); }
  .card__art { position: absolute; inset: 0; }

  .wordmark { position: absolute; line-height: 1; }
  .wordmark__name { display: block; font-weight: 300; letter-spacing: 2px; }
  .wordmark__tag { display: block; font-weight: 300; text-transform: lowercase; }
  .card--front .wordmark { left: 34px; top: 14px; color: var(--ink); }
  .card--front .wordmark__name { font-size: 80px; }
  .card--front .wordmark__tag { font-size: 10px; letter-spacing: 7px; color: var(--muted); margin-top: 2px; }
  .card--back .wordmark { left: 0; right: 0; top: 78px; text-align: center; color: var(--logo-light); }
  .card--back .wordmark__name { font-size: 104px; }
  .card--back .wordmark__tag { font-size: 12px; letter-spacing: 9px; margin-top: 6px; }

  .contact {
    position: absolute; left: 62px; top: 122px; list-style: none;
    font-size: 11px; color: var(--ink); line-height: 17px;
  }
  .contact__item { display: flex; align-items: center; gap: 6px; }
  .contact__icon { width: 11px; height: 11px; flex: none; }

  .person { position: absolute; right: 30px; top: 56px; text-align: right; }
  .person__name { font-size: 28px; line-height: 1.1; color: var(--earth); font-weight: 400; }
  .person__first { color: var(--water); font-weight: 600; }
  .person__role { font-size: 14px; font-weight: 500; color: var(--ink); }

  .abn {
    position: absolute; left: 214px; bottom: 12px;
    font-size: 14px; color: var(--paper); letter-spacing: 0.5px;
  }
</style>
</head>
<body>
<main class="stage">
  <section class="card card--front" aria-label="Business card front">
    <svg class="card__art" viewBox="0 0 520 297" aria-hidden="true">
      <path d="M0,150 C18,236 120,258 250,258 C340,258 410,250 446,297 L0,297 Z" fill="var(--water)"/>
      <path d="M16,118 C22,190 70,232 142,256" fill="none" stroke="var(--earth)" stroke-width="5" stroke-linecap="round"/>
      <rect x="506" y="128" width="14" height="52" fill="var(--earth)"/>
    </svg>
    <div class="wordmark">
      <span class="wordmark__name">tbk</span>
      <span class="wordmark__tag">plumbing services</span>
    </div>
    <ul class="contact">
      <li class="contact__item">
        <svg class="contact__icon" viewBox="0 0 12 12"><path d="M3 1 L5 3.5 L4 5 C5 7 6 8 7.5 8.5 L9 7.5 L11 9.5 L9.5 11 C5 10.5 1.5 7 1 2.5 Z" fill="var(--water)"/></svg>
        0431 286 517
      </li>
      <li class="contact__item">
        <svg class="contact__icon" viewBox="0 0 12 12"><circle cx="6" cy="6" r="5" fill="none" stroke="var(--water)" stroke-width="1.3"/><path d="M1 6 H11 M6 1 C3 4 3 8 6 11 C9 8 9 4 6 1" fill="none" stroke="var(--water)" stroke-width="1"/></svg>
        www.tbk-plumbing.com.au
      </li>
      <li class="contact__item">
        <svg class="contact__icon" viewBox="0 0 12 12"><rect x="1" y="2.5" width="10" height="7" rx="1" fill="var(--water)"/><path d="M1.5 3 L6 6.5 L10.5 3" fill="none" stroke="#fff" stroke-width="1"/></svg>
        rowan@tbk-plumbing.com.au
      </li>
    </ul>
    <div class="person">
      <p class="person__name"><span class="person__first">Rowan</span> Keddle</p>
      <p class="person__role">Director</p>
    </div>
    <p class="abn">ABN - 73 215 904 386</p>
  </section>

  <section class="card card--back" aria-label="Business card back">
    <div class="wordmark">
      <span class="wordmark__name">tbk</span>
      <span class="wordmark__tag">plumbing services</span>
    </div>
  </section>
</main>
</body>
</html>
```